FinTech company looking to revamp and expand client-facing interface for our financial models

Pellworth Engines currently has a very simple website that allows clients to interact with our financial models. We are looking to completely redesign the current site and add several extra pages to provide extra functionality. We want the design to have a modern, slick feel, that will work on both a desktop or a tablet. It should be straightforward for clients to move between different pages at any time, and clear from the layout how to interact with the more advanced features. We have included screenshots of existing pages in the attached design brief, as well as sketches of the functionality required by the new pages, but can't provide a direct link to the current site.
Target Market(s)
Professional investors that will be paying to access the interface
Industry/Entity Type
Finance
Number of Pages Required
4 page
Colors
Designer to choose colors to be used in the design.
Look and feel
Each slider illustrates characteristics of the customer's brand and the style your logo design should communicate.

```html
<!DOCTYPE html>
<html lang="en">
<head>
<meta charset="utf-8">
<title>Pellworth Engines — Models</title>
<link href="https://fonts.googleapis.com/css2?family=Open+Sans:wght@400;600;700&display=swap" rel="stylesheet">
<style>
  :root {
    --ink: #231f20;
    --ink-deep: #1a1718;
    --gold: #fdc41f;
    --gold-band: #fcc61f;
    --font: "Open Sans", sans-serif;
  }
  * { margin: 0; padding: 0; box-sizing: border-box; }
  html, body { width: 1200px; height: 1124px; overflow: hidden; }
  body { background: var(--ink); color: var(--gold); font-family: var(--font); position: relative; }
  .abs { position: absolute; }

  .rule { position: absolute; left: 2px; right: 0; height: 3px; background: var(--gold); }

  .range-tabs { top: 116px; left: 126px; display: flex; gap: 8px; font-size: 19px; font-weight: 600; letter-spacing: 2.5px; }
  .range-tabs span { padding: 1px 11px; }
  .range-tabs .is-active { background: var(--ink-deep); }

  .brand { font-weight: 700; letter-spacing: 0.5px; display: flex; align-items: center; gap: 10px; line-height: 26px; }
  .brand .dot { width: 14px; height: 14px; border-radius: 50%; background: currentColor; flex: none; }
  .brand-header { top: 103px; left: 540px; font-size: 22px; color: var(--gold); }

  .main-nav { top: 122px; left: 704px; display: flex; font-size: 13px; font-weight: 600; letter-spacing: 1.8px; }
  .main-nav a { color: var(--gold); text-decoration: none; display: flex; align-items: center; gap: 9px; }
  .main-nav a + a { margin-left: 28px; }
  .main-nav a.fav { margin-left: 42px; }
  .main-nav svg { width: 17px; height: 17px; fill: var(--gold); }

  .filter { left: 138px; display: flex; align-items: center; }
  .filter .label { font-size: 13px; font-weight: 600; letter-spacing: 1.5px; width: 88px; }
  .filter .label small { font-size: 10px; }
  .filter .key { font-size: 19px; font-weight: 700; letter-spacing: 2px; width: 113px; }
  .filter .field { width: 138px; height: 18px; border: 1.5px solid var(--gold); font-size: 11px; font-weight: 700; padding-left: 8px; line-height: 15px; }

  .models { position: absolute; top: 395px; left: 106px; width: 989px; height: 420px; }
  .col { position: absolute; white-space: nowrap; }
  .thead { height: 42px; border-bottom: 3px solid var(--gold); font-size: 16px; font-weight: 600; letter-spacing: 2px; position: relative; }
  .thead .col { top: 0; }
  .thead .id { font-size: 21px; font-weight: 600; top: -4px; display: flex; align-items: center; gap: 10px; }
  .thead .id svg { width: 12px; height: 7px; fill: var(--gold); }
  .row { position: absolute; left: 0; width: 100%; font-size: 19px; font-weight: 600; letter-spacing: 2px; line-height: 22px; }

  .c-id { left: 24px; } .c-sector { left: 159px; } .c-time { left: 336px; }
  .c-q { left: 502px; } .c-s1 { left: 626px; } .c-s2 { left: 744px; } .c-s3 { left: 864px; }

  .site-footer { position: absolute; left: 0; top: 914px; width: 1200px; height: 210px; background: var(--gold-band); color: var(--ink); }
  .brand-footer { top: 76px; left: 160px; font-size: 22px; color: var(--ink); }
  .contact { top: 31px; left: 371px; font-size: 15px; font-weight: 600; letter-spacing: 1.5px; line-height: 20px; }
  .site-footer h3 { font-size: 19px; font-weight: 700; letter-spacing: 2.5px; margin-bottom: 4px; }
  .contact .indent { padding-left: 47px; }
  .divider { top: 24px; left: 689px; width: 1px; height: 120px; background: var(--ink); }
  .follow { top: 31px; left: 715px; }
  .socials { display: flex; gap: 22px; margin-top: 6px; }
  .socials span { width: 30px; height: 30px; border-radius: 50%; background: var(--ink); display: block; }
  .newsletter { margin-top: 11px; display: flex; align-items: flex-start; gap: 9px; }
  .newsletter .caption { font-size: 13px; font-weight: 600; letter-spacing: 1.5px; border-top: 1px solid var(--ink); border-bottom: 1px solid var(--ink); padding: 1px 2px; }
  .newsletter .email { width: 202px; height: 21px; background: var(--ink); color: var(--gold); font-size: 13px; font-weight: 600; letter-spacing: 1.5px; padding-left: 15px; line-height: 21px; }
</style>
</head>
<body>
  <div class="rule" style="top:34px"></div>
  <div class="rule" style="top:41px"></div>

  <nav class="abs range-tabs">
    <span>QBOOS</span><span class="is-active">250D</span><span>83D</span><span>42D</span>
  </nav>

  <div class="abs brand brand-header"><span class="dot"></span><span>Pellworth<br>Engines</span></div>

  <nav class="abs main-nav">
    <a href="#"><svg viewBox="0 0 20 20"><path d="M10 2 1 10h3v8h4.5v-5h3v5H16v-8h3z"/></svg>MODELS</a>
    <a href="#"><svg viewBox="0 0 20 20"><circle cx="10" cy="10" r="2.5"/><ellipse cx="10" cy="10" rx="9" ry="3.5" fill="none" stroke="#fdc41f" stroke-width="1.4"/><ellipse cx="10" cy="10" rx="9" ry="3.5" fill="none" stroke="#fdc41f" stroke-width="1.4" transform="rotate(60 10 10)"/><ellipse cx="10" cy="10" rx="9" ry="3.5" fill="none" stroke="#fdc41f" stroke-width="1.4" transform="rotate(-60 10 10)"/></svg>SENTIVITITES</a>
    <a href="#" class="fav"><svg viewBox="0 0 20 20"><path d="m10 1.5 2.6 5.6 6 .7-4.5 4.1 1.2 6L10 14.9l-5.3 3 1.2-6L1.4 7.8l6-.7z"/></svg>FAVOURITES</a>
  </nav>

  <div class="rule" style="top:219px"></div>
  <div class="rule" style="top:226px"></div>

  <div class="abs filter" style="top:322px"><span class="label">Quality</span><span class="key">Treshold:</span><span class="field">-10</span></div>
  <div class="abs filter" style="top:354px"><span class="label">Abs. <small>stat</small></span><span class="key">Treshold:</span><span class="field">-10</span></div>

  <section class="models">
    <div class="thead">
      <span class="col c-id id">ID <svg viewBox="0 0 12 7"><path d="M0 0h12L6 7z"/></svg></span>
      <span class="col" style="left:179px">Sector</span>
      <span class="col" style="left:365px">Time</span>
      <span class="col" style="left:506px">Quality</span>
      <span class="col" style="left:640px">Stat 1</span>
      <span class="col" style="left:748px">Stat 2</span>
      <span class="col" style="left:871px">Stat 3</span>
    </div>

    <div class="row" style="top:82px">
      <span class="col c-id">Model 1</span><span class="col c-sector">Materials</span>
      <span class="col c-time">2019-07-03<br>12:15:00.000</span>
      <span class="col c-q" style="top:2px">30.2288</span><span class="col c-s1">2.01574</span>
      <span class="col c-s2">23.305</span><span class="col c-s3" style="left:857px">-0.149368</span>
    </div>
    <div class="row" style="top:145px">
      <span class="col c-id">Model 2</span><span class="col c-sector" style="left:161px">Industrails</span>
      <span class="col c-time" style="top:2px">2019-07-03<br>12:15:00.000</span>
      <span class="col c-q" style="top:3px">32.8964</span><span class="col c-s1" style="left:624px;top:2px">0.87307</span>
      <span class="col c-s2" style="top:1px">32.185</span><span class="col c-s3" style="left:860px;top:-3px">-0.0336927</span>
    </div>
    <div class="row" style="top:210px">
      <span class="col c-id" style="top:6px">Model 3</span><span class="col c-sector">Consumer<br>Discretionary</span>
      <span class="col c-time" style="top:2px">2019-07-03<br>12:15:00.000</span>
      <span class="col c-q" style="top:8px">1.66002</span><span class="col c-s1" style="left:614px;top:1px">-0.569222</span>
      <span class="col c-s2" style="top:1px">159.814</span><span class="col c-s3" style="top:1px">0.0252328</span>
    </div>
    <div class="row" style="top:280px">
      <span class="col c-id" style="top:-2px">Model 4</span><span class="col c-sector">Information<br>Technology</span>
      <span class="col c-time">2019-07-03<br>12:15:00.000</span>
      <span class="col c-q">45.6856</span><span class="col c-s1" style="left:624px">0.412148</span>
      <span class="col c-s2" style="top:-2px">202.488</span><span class="col c-s3" style="top:-2px">0.0849232</span>
    </div>
    <div class="row" style="top:351px">
      <span class="col c-id" style="top:-2px">Model 5</span><span class="col c-sector">Information<br>Technology</span>
      <span class="col c-time" style="top:2px">2019-07-03<br>12:15:00.000</span>
      <span class="col c-q" style="top:2px">75.7733</span><span class="col c-s1" style="left:624px;top:-1px">7.06728</span>
      <span class="col c-s2" style="top:-1px">188.605</span><span class="col c-s3" style="top:-2px">0.016913</span>
    </div>
  </section>

  <footer class="site-footer">
    <div class="abs brand brand-footer"><span class="dot"></span><span>Pellworth<br>Engines</span></div>
    <div class="abs contact">
      <h3>Contact</h3>
      <p>Phone: 415 555 0142</p>
      <p>Email: info@pellworth.com</p>
      <p style="margin-top:3px">Add: 27 Harrow Lane, Suite 4</p>
      <p class="indent">Fairview, Ca 94000</p>
    </div>
    <div class="abs divider"></div>
    <div class="abs follow">
      <h3>Follow</h3>
      <div class="socials">
        <span aria-label="Social link 1"></span><span aria-label="Social link 2"></span>
        <span aria-label="Social link 3"></span><span aria-label="Social link 4"></span>
      </div>
      <div class="newsletter"><span class="caption">News Letters</span><span class="email">Enter Your Email</span></div>
    </div>
  </footer>
</body>
</html>
```